An image to show that our fees are offset by our good management

We work in the property sector.
We'd like a slide showing that our fees weigh very little compared with the savings we can generate if we do our job properly as property managers.
To do this, we've come up with a slide with a scale showing our fees on the left (which weigh less or the same) than the items on the right.
On the right you can see:
Savings on building maintenance costs
Savings on running costs
Optimization of vacant periods
Good monitoring of disputes to avoid rental losses
We welcome any other ideas you may have to highlight this concept (even off-balance sheet).

```html
<!DOCTYPE html>
<html lang="en">
<head>
<meta charset="UTF-8">
<title>Balance Chart – Fees vs Savings</title>
<link rel="stylesheet" href="https://fonts.googleapis.com/css2?family=Arimo:wght@700&family=Open+Sans:wght@600&display=swap">
<style>
  :root {
    --bg-center: #f1f0de;
    --bg-edge: #ddcfb1;
    --heading: #b09683;
    --wood-light: #dfac72;
    --wood-mid: #c99a6c;
    --wood-dark: #b48c66;
    --wood-band-light: #b98548;
    --wood-band-dark: #956842;
    --pill-text: #7b5c3c;
    --fee-dark: #5f3612;
    --fee-text: #f6d8b2;
    --pill-edge: #6e5634;
    --icon: #9c7857;
    --shadow: rgba(120, 100, 70, 0.18);
  }
  html, body {
    margin: 0;
    padding: 0;
    width: 1200px;
    height: 900px;
    overflow: hidden;
  }
  .slide {
    position: relative;
    width: 1200px;
    height: 900px;
    background: radial-gradient(ellipse 60% 62% at 50% 45%, var(--bg-center) 0%, #ece9d4 55%, var(--bg-edge) 100%);
    font-family: "Open Sans", Arial, sans-serif;
    font-weight: 600;
    overflow: hidden;
  }
  .title {
    position: absolute;
    left: 0;
    width: 100%;
    text-align: center;
    font-family: "Arimo", Arial, sans-serif;
    font-weight: 700;
    color: var(--heading);
    margin: 0;
    line-height: 1;
  }
  .title-main { top: 36px; font-size: 113px; letter-spacing: 1px; }
  .title-sub { top: 148px; font-size: 57px; }

  .floor-shadow {
    position: absolute;
    left: 213px;
    top: 681px;
    width: 770px;
    height: 44px;
    border-radius: 50%;
    background: radial-gradient(ellipse at center, var(--shadow) 0%, rgba(120,100,70,0.08) 60%, transparent 100%);
  }
  .beam {
    position: absolute;
    left: 141px;
    top: 489px;
    width: 914px;
    height: 63px;
    border: 1px solid #e7c08e;
    box-sizing: border-box;
    background: linear-gradient(to right, var(--wood-light), var(--wood-mid) 55%, var(--wood-dark));
  }
  .beam::after {
    content: "";
    position: absolute;
    left: 0; right: 0; bottom: 0;
    height: 20px;
    background: linear-gradient(to right, var(--wood-band-light), #a87646 55%, var(--wood-band-dark));
  }
  .pedestal {
    position: absolute;
    left: 540px;
    top: 464px;
    width: 114px;
    height: 216px;
    border-radius: 57px 57px 0 0;
    border: 1px solid #e7c08e;
    box-sizing: border-box;
    background: linear-gradient(to right, #dcab73, #cfa072 55%, #bb9068);
  }
  .pedestal::after {
    content: "";
    position: absolute;
    left: 0; right: 0; bottom: 0;
    height: 8px;
    background: #a77447;
  }
  .pivot {
    position: absolute;
    left: 571px;
    top: 495px;
    width: 52px;
    height: 52px;
    border-radius: 50%;
    box-sizing: border-box;
    border: 2px solid #a7784a;
    background: radial-gradient(circle at 50% 45%, #e8b780, #d8a46c);
  }
  .pedestal-icon {
    position: absolute;
    left: 552px;
    top: 570px;
    width: 94px;
    height: 88px;
  }
  .base {
    position: absolute;
    left: 426px;
    top: 681px;
    width: 344px;
    height: 20px;
    border-radius: 8px 8px 0 0;
    background: linear-gradient(to bottom, #dfae78, #c79a6e);
  }

  .pill {
    position: absolute;
    width: 294px;
    height: 55px;
    border-radius: 28px;
    box-sizing: border-box;
    border: 1.5px solid var(--pill-edge);
    display: flex;
    align-items: center;
    justify-content: center;
    text-align: center;
    white-space: nowrap;
    box-shadow: 3px 3px 6px rgba(90, 70, 40, 0.25);
  }
  .pill-saving {
    background: linear-gradient(to right, #d9a870, #dcaa72 40%, #b89068);
    color: var(--pill-text);
    font-size: 19.5px;
    line-height: 23px;
    letter-spacing: -0.3px;
  }
  .pill-fees {
    left: 100px;
    top: 432px;
    background: linear-gradient(to right, #a88058, #a57a4e 50%, var(--fee-dark));
    color: var(--fee-text);
    font-size: 24px;
    border-color: #c7a070;
  }
  .pill-maintenance { left: 802px; top: 266px; transform: rotate(-2.5deg); }
  .pill-running { left: 863px; top: 321px; transform: rotate(1deg); padding-left: 40px; }
  .pill-vacancy { left: 799px; top: 375px; }
  .pill-disputes { left: 778px; top: 432px; }

  .tagline {
    position: absolute;
    left: 0;
    top: 808px;
    width: 100%;
    text-align: center;
    color: var(--heading);
    font-size: 19px;
    letter-spacing: -0.2px;
    margin: 0;
  }
</style>
</head>
<body>
  <main class="slide">
    <h1 class="title title-main">Balance</h1>
    <h2 class="title title-sub">Chart</h2>

    <div class="floor-shadow"></div>
    <div class="beam"></div>
    <div class="pedestal"></div>
    <div class="pivot"></div>
    <svg class="pedestal-icon" viewBox="0 0 94 88" role="img" aria-label="Property management icon: a house">
      <g fill="var(--icon)">
        <polygon points="47,10 86,44 79,50 47,22 15,50 8,44"/>
        <rect x="71" y="12" width="7" height="20"/>
        <path d="M20 47 L47 24 L74 47 V80 H20 Z"/>
      </g>
      <path d="M39 80 V60 a8 8 0 0 1 16 0 V80 Z" fill="#c59767"/>
    </svg>
    <div class="base"></div>

    <div class="pill pill-fees">Our fees</div>

    <div class="pill pill-saving pill-maintenance">Savings on building<br>maintenance costs</div>
    <div class="pill pill-saving pill-running">Savings on<br>running costs</div>
    <div class="pill pill-saving pill-vacancy">Optimization of<br>vacant periods</div>
    <div class="pill pill-saving pill-disputes">Good monitoring of disputes<br>to avoid rental losses</div>

    <p class="tagline">Our Fees Weigh Very Little Compared With the Savings We Can As Property Managers.</p>
  </main>
</body>
</html>
```